VOMRA Pty Ltd Business Card

Looking for a simple yet eye-catching double-sided business card design using my company logo on one side and contact details on the other.

Target Market(s)

Government

Industry/Entity Type

Communication Systems Engineering

Contact Information for Business Card

VOMRA Pty Ltd

Requirements
Nice to have
• Would be great to have a QR code so details can be scanned into contacts

```html
<!DOCTYPE html>
<html lang="en">
<head>
<meta charset="utf-8">
<title>VOMRA Pty Ltd Business Card</title>
<link rel="stylesheet" href="https://fonts.googleapis.com/css2?family=Open+Sans:wght@400;600;700;800&display=swap">
<style>
  :root {
    --stage: #26292d;
    --slate: #343c42;
    --paper: #ebebeb;
    --ink: #0d0f10;
    --white: #ffffff;
  }
  * { box-sizing: border-box; margin: 0; padding: 0; }
  html, body {
    width: 1200px; height: 780px; overflow: hidden;
    background: var(--stage);
    font-family: "Open Sans", Arial, sans-serif;
  }
  .sheet {
    position: relative; width: 1200px; height: 780px;
    display: flex; align-items: center; justify-content: center; gap: 40px;
  }
  .card {
    position: relative; width: 540px; height: 310px; overflow: hidden;
    box-shadow: 0 10px 30px rgba(0,0,0,.45);
  }

  /* Front: contact side */
  .card--front { background: var(--paper); }
  .front__panel {
    position: absolute; left: 0; top: 118px; width: 330px; bottom: 0;
    background: var(--slate);
  }
  .front__tab {
    position: absolute; right: 0; top: 196px; width: 22px; height: 50px;
    background: var(--slate);
  }
  .front__brand {
    position: absolute; left: 40px; top: 34px;
    display: flex; align-items: center; gap: 14px;
  }
  .brand-dot {
    width: 22px; height: 22px; border-radius: 50%; background: var(--slate);
  }
  .brand-name {
    font-weight: 800; font-size: 46px; letter-spacing: 2px;
    color: var(--slate); line-height: 1;
  }
  .front__person {
    position: absolute; right: 32px; top: 150px; text-align: right; color: var(--ink);
  }
  .person__name { font-weight: 700; font-size: 27px; line-height: 1.1; }
  .person__role { font-weight: 400; font-size: 15px; margin-top: 2px; }
  .contact {
    position: absolute; left: 24px; top: 132px; color: var(--white);
    font-size: 12.5px; line-height: 1.5; list-style: none;
  }
  .contact li { display: flex; align-items: center; gap: 7px; }
  .contact .contact__address { padding-left: 19px; }
  .contact svg { width: 12px; height: 12px; flex: none; }

  /* Back: brand side */
  .card--back {
    background: var(--slate);
    display: flex; align-items: center; justify-content: center; gap: 22px;
  }
  .card--back .brand-dot { width: 40px; height: 40px; background: var(--white); }
  .card--back .brand-name { color: var(--white); font-size: 88px; letter-spacing: 4px; }
</style>
</head>
<body>
<main class="sheet">
  <section class="card card--front" aria-label="Business card front with contact details">
    <div class="front__panel"></div>
    <div class="front__tab"></div>
    <div class="front__brand">
      <span class="brand-dot"></span>
      <span class="brand-name">VOMRA</span>
    </div>
    <div class="front__person">
      <p class="person__name">Jordan Pell</p>
      <p class="person__role">Co-Founder</p>
    </div>
    <ul class="contact">
      <li class="contact__address">14-16 Harlow Lane Redfern Park</li>
      <li class="contact__address">NSW 2016 Australia</li>
      <li>
        <svg viewBox="0 0 12 12" aria-hidden="true"><path fill="#fff" d="M2.3 1h2l1 2.6-1.3.9a6.5 6.5 0 0 0 3.5 3.5l.9-1.3 2.6 1v2c0 .7-.6 1.3-1.3 1.3A9.7 9.7 0 0 1 1 2.3C1 1.6 1.6 1 2.3 1z"/></svg>
        (02) 5550 1482
      </li>
      <li>
        <svg viewBox="0 0 12 12" aria-hidden="true"><circle cx="6" cy="6" r="5" fill="none" stroke="#fff" stroke-width="1.2"/><path d="M1 6h10M6 1c2 2.5 2 7.5 0 10M6 1c-2 2.5-2 7.5 0 10" fill="none" stroke="#fff" stroke-width="1"/></svg>
        www.vomra.com.au
      </li>
      <li>
        <svg viewBox="0 0 12 12" aria-hidden="true"><rect x="1" y="2.5" width="10" height="7" fill="none" stroke="#fff" stroke-width="1.2"/><path d="M1 2.5l5 4 5-4" fill="none" stroke="#fff" stroke-width="1.2"/></svg>
        admin@vomra.com.au
      </li>
    </ul>
  </section>

  <section class="card card--back" aria-label="Business card back with company name">
    <span class="brand-dot"></span>
    <span class="brand-name">VOMRA</span>
  </section>
</main>
</body>
</html>
```